Corporate Business Card

Very professional, Modern, Not to busy, include phone address email, website
(253) 617-4930, 18761 52nd Avenue S, Kent, WA 98047, martin@plumlinegroup.com, varkoworks.com

Target Market(s)

Manufacturing

Industry/Entity Type

Aero, machining, manufacturing, Off road racing

Contact Information for Business Card

Phone, address email, website

```html
<!DOCTYPE html>
<html lang="en">
<head>
<meta charset="utf-8">
<title>Varko Works – Business Card</title>
<link href="https://fonts.googleapis.com/css2?family=Exo+2:wght@700&family=Lato:wght@400&display=swap" rel="stylesheet">
<style>
  :root {
    --backdrop: #2b2b2d;
    --card: #ffffff;
    --card-shade: #ececec;
    --navy: #1d3a72;
    --red: #d1222b;
    --ink: #444448;
  }
  * { box-sizing: border-box; margin: 0; padding: 0; }
  html, body { width: 1200px; height: 900px; overflow: hidden; }
  body {
    background: var(--backdrop);
    font-family: "Lato", sans-serif;
    position: relative;
  }
  .card {
    position: absolute;
    left: 250px;
    width: 700px;
    height: 400px;
    background: linear-gradient(135deg, var(--card-shade) 0%, var(--card) 55%, var(--card) 100%);
    overflow: hidden;
  }
  .card--front { top: 40px; }
  .card--back { top: 470px; }
  .card__bands { position: absolute; inset: 0; width: 700px; height: 400px; }
  .band--navy { fill: var(--navy); }
  .band--red { fill: var(--red); }

  .wordmark { position: absolute; }
  .wordmark__name {
    font-family: "Exo 2", sans-serif;
    font-weight: 700;
    color: var(--navy);
    font-size: 50px;
    letter-spacing: 1px;
    line-height: 1;
    white-space: nowrap;
  }
  .wordmark__rule {
    height: 2px;
    background: var(--navy);
    width: 230px;
    margin-top: 14px;
  }
  .card--front .wordmark { left: 48px; top: 298px; }
  .card--back .wordmark { left: 300px; top: 62px; }

  .contact {
    position: absolute;
    left: 80px;
    top: 256px;
    list-style: none;
    color: var(--ink);
    font-size: 19px;
  }
  .contact__item {
    display: flex;
    align-items: center;
    gap: 8px;
    height: 38px;
  }
  .contact__icon { width: 18px; height: 18px; fill: var(--red); flex: none; }
  .contact__icon--line { fill: none; stroke: var(--red); stroke-width: 2; }
  .contact__divider {
    width: 1.5px; height: 20px; background: var(--navy); margin: 0 6px;
  }
</style>
</head>
<body>

<section class="card card--front">
  <svg class="card__bands" viewBox="0 0 700 400" aria-hidden="true">
    <polygon class="band--navy" points="330,196 700,196 700,210 344,210"/>
    <polygon class="band--red" points="352,232 700,232 700,246 366,246"/>
    <polygon class="band--red" points="374,268 700,268 700,282 388,282"/>
  </svg>
  <div class="wordmark">
    <div class="wordmark__name">Varko Works</div>
    <div class="wordmark__rule"></div>
  </div>
</section>

<section class="card card--back">
  <svg class="card__bands" viewBox="0 0 700 400" aria-hidden="true">
    <polygon class="band--navy" points="0,266 48,266 38,280 0,280"/>
    <polygon class="band--red" points="0,304 58,304 48,318 0,318"/>
    <polygon class="band--red" points="0,342 68,342 58,356 0,356"/>
  </svg>
  <div class="wordmark">
    <div class="wordmark__name">Varko Works</div>
    <div class="wordmark__rule"></div>
  </div>
  <ul class="contact">
    <li class="contact__item">
      <svg class="contact__icon" viewBox="0 0 20 20" aria-hidden="true"><path d="M2 8c0-3 4-5 8-5s8 2 8 5l-4 1-1-2H7L6 9 2 8zm3 2h10l1 7H4l1-7z"/></svg>
      <span>(253) 617-4930</span>
    </li>
    <li class="contact__item">
      <svg class="contact__icon" viewBox="0 0 20 20" aria-hidden="true"><path d="M10 1a6 6 0 0 0-6 6c0 5 6 12 6 12s6-7 6-12a6 6 0 0 0-6-6zm0 8.5A2.5 2.5 0 1 1 10 4.5a2.5 2.5 0 0 1 0 5z"/></svg>
      <span>18761 52nd Avenue S, Kent, WA 98047</span>
    </li>
    <li class="contact__item">
      <svg class="contact__icon" viewBox="0 0 20 20" aria-hidden="true"><path d="M2 8l8-6 8 6v10H2V8zm2 1.5V16h12V9.5l-6 4-6-4z"/></svg>
      <span>martin@plumlinegroup.com</span>
      <span class="contact__divider"></span>
      <svg class="contact__icon contact__icon--line" viewBox="0 0 20 20" aria-hidden="true"><circle cx="10" cy="10" r="8"/><ellipse cx="10" cy="10" rx="3.5" ry="8"/><path d="M2 10h16"/></svg>
      <span>www.varkoworks.com</span>
    </li>
  </ul>
</section>

</body>
</html>
```